Specialised investor in e-mobility and energy wants business card design

We need a business card design that fits our existing corporate design. <The look and feel must be 'sharp'/'clean', dynamic, communicate momentum, professionalism etc (as one would imagine from a firm in the financial sector). We like the idea of a reverse-side of the card that includes the logo, and the name and contact details on the other. We expect the deliverable to be whatever format might be required to be able to get cards printed directly by a service such as kelmo press. Our website is www.zub.capital

```html
<!DOCTYPE html>
<html lang="en">
<head>
<meta charset="utf-8">
<title>ZUB Capital – Business Card</title>
<link href="https://fonts.googleapis.com/css2?family=Poppins:wght@300;400;600&display=swap" rel="stylesheet">
<style>
  :root {
    --bg: #1e1e1e;
    --green-light: #86b34c;
    --green-mid: #5e8a36;
    --green-deep: #2f4f22;
    --white: #ffffff;
  }
  * { margin: 0; padding: 0; box-sizing: border-box; }
  html, body {
    width: 1200px; height: 1015px; overflow: hidden;
    background: var(--bg);
    font-family: "Poppins", sans-serif;
  }
  .stage {
    position: relative; width: 1200px; height: 1015px;
    display: flex; flex-direction: column; align-items: center; justify-content: center; gap: 60px;
  }
  .card {
    position: relative; width: 580px; height: 332px; overflow: hidden;
    box-shadow: 0 14px 30px rgba(0,0,0,.55);
  }
  .card--front {
    background: linear-gradient(180deg, var(--green-light) 0%, var(--green-mid) 45%, var(--green-deep) 100%);
    display: flex; align-items: center; justify-content: center;
  }
  .wordmark {
    font-weight: 300; letter-spacing: 1px; line-height: 1;
  }
  .card--front .wordmark { color: var(--white); font-size: 64px; }
  .card--back { background: var(--white); }
  .card--back .curve { position: absolute; inset: 0; width: 100%; height: 100%; }
  .card--back .wordmark {
    position: absolute; top: 46px; right: 40px;
    color: var(--green-deep); font-size: 44px;
  }
  .contact {
    position: absolute; left: 34px; bottom: 26px; color: var(--white);
  }
  .contact__name {
    color: var(--green-light); font-weight: 600; font-size: 21px; letter-spacing: .5px; line-height: 1.1;
  }
  .contact__role { font-size: 14px; font-weight: 400; margin-bottom: 12px; }
  .contact__list { list-style: none; font-size: 14px; line-height: 1.5; }
  .contact__list li { display: flex; align-items: center; gap: 10px; }
  .contact__list svg { width: 14px; height: 14px; flex: none; }
  .contact__address { font-size: 14px; line-height: 1.3; margin-top: 12px; padding-left: 24px; }
</style>
</head>
<body>
<main class="stage">
  <section class="card card--front">
    <span class="wordmark">ZUB Capital</span>
  </section>

  <section class="card card--back">
    <svg class="curve" viewBox="0 0 580 332" preserveAspectRatio="none" aria-hidden="true">
      <path d="M0,118 C130,30 350,50 500,332 L0,332 Z" fill="var(--green-light)"/>
      <path d="M0,128 C125,48 330,62 470,332 L0,332 Z" fill="var(--green-deep)"/>
    </svg>
    <span class="wordmark">ZUB Capital</span>
    <div class="contact">
      <p class="contact__name">MARCUS HALE</p>
      <p class="contact__role">Managing Director</p>
      <ul class="contact__list">
        <li>
          <svg viewBox="0 0 24 24"><path fill="var(--green-light)" d="M6.6 10.8a15 15 0 0 0 6.6 6.6l2.2-2.2a1 1 0 0 1 1-.25 11.4 11.4 0 0 0 3.6.57 1 1 0 0 1 1 1V20a1 1 0 0 1-1 1A17 17 0 0 1 3 4a1 1 0 0 1 1-1h3.5a1 1 0 0 1 1 1c0 1.25.2 2.45.57 3.57a1 1 0 0 1-.25 1z"/></svg>
          055-210 884 316
        </li>
        <li>
          <svg viewBox="0 0 24 24"><path fill="var(--green-light)" d="M2 5h20v14H2z"/><path fill="none" stroke="var(--green-deep)" stroke-width="1.8" d="M2 5l10 8 10-8"/></svg>
          hello@zub.capital
        </li>
        <li>
          <svg viewBox="0 0 24 24" fill="none" stroke="var(--green-light)" stroke-width="2"><circle cx="12" cy="12" r="9.5"/><path d="M2.5 12h19M12 2.5c3 3 3 16 0 19M12 2.5c-3 3-3 16 0 19"/></svg>
          www.zub.capital
        </li>
      </ul>
      <p class="contact__address">18, Voltway Avenue<br>60311, Freeland</p>
    </div>
  </section>
</main>
</body>
</html>
```